Business Card Design Project for a Restaurant/Wine Bar

New, fresh business card design for Brevenna Wine Bar & Restaurant, Bandon, Oregon. We are an established restaurant on the Oregon coast featuring "Italian coastal cuisine."

"Brevenna" means bay leaf in Italian. We aren't sure if we would like our logo on the card or not, but if you have something interesting that uses it, then please do so. The basic information is essential - full restaurant name, address, phone and website (do not use www). The font on our menu and wine list may give you some sort of an idea of our style.

One-sided card needed as we often use the backside to write down various types of info for customers.
Updates

After seeing a few submissions, we would like to see what designers can come up with-using the logo, just the leaf, or none at all. Sky is the limit as long as our full restaurant name, address, phone and website (please leave out www) are there. Please contact us if questions!

I appreciate all of your designs! Our deadline is next week, but I will continue to give feedback on designs as I can. This is our busiest season, so my co-owner/chef/husband, won't have time to look at the designs for awhile. When he does, we can make our decision.

cheers,
Maren

Target Market(s)

Fine dining/wine crowd. Would like something simple and elegant, but not pretentious or stuffy. Brevenna means bay laurel (bay leaf) in Italian (please see our logo).

Industry/Entity Type

Restaurant

Requirements
Must have
• Full Name of Restaurant: Brevenna Wine Bar & Restaurant
Address: 812 4th Ave NW, Calder Bay, Norland 00123
Phone: 541.555.0172
website: brevennawinebar.example (do not use www)
Should not have
• Loud colors.

```html
<!DOCTYPE html>
<html lang="en">
<head>
<meta charset="utf-8">
<title>Brevenna Wine Bar &amp; Restaurant – Business Card</title>
<link rel="stylesheet" href="https://fonts.googleapis.com/css2?family=Open+Sans:wght@400;600;700&display=swap">
<style>
  :root {
    --backdrop: #ece9e2;
    --card: #ffffff;
    --band: #a9a9a9;
    --ink: #1a1a1a;
    --ink-soft: #2b2b2b;
    --rule: #111111;
  }
  * { margin: 0; padding: 0; box-sizing: border-box; }
  html, body {
    width: 1200px;
    height: 801px;
    overflow: hidden;
    background: var(--backdrop);
    font-family: "Open Sans", Arial, sans-serif;
  }
  .business-card {
    position: absolute;
    left: 100px;
    top: 120px;
    width: 1000px;
    height: 560px;
    border-radius: 42px;
    background: var(--card);
    overflow: hidden;
    box-shadow: 0 6px 24px rgba(0,0,0,0.18);
  }
  .card-shapes {
    position: absolute;
    inset: 0;
    width: 100%;
    height: 100%;
  }
  .wordmark {
    position: absolute;
    left: 0;
    right: 0;
    top: 60px;
    text-align: center;
    color: var(--ink);
    font-weight: 700;
    font-size: 74px;
    line-height: 1.05;
    letter-spacing: 2px;
    text-transform: uppercase;
  }
  .restaurant-name {
    position: absolute;
    left: 115px;
    width: 800px;
    top: 382px;
    text-align: center;
    color: var(--ink-soft);
    font-weight: 700;
    font-size: 29px;
  }
  .contact {
    position: absolute;
    color: var(--ink-soft);
    font-size: 21px;
    line-height: 33px;
    font-weight: 400;
  }
  .contact-left { left: 200px; top: 458px; }
  .contact-right { left: 578px; top: 440px; }
  .contact-line { display: flex; align-items: center; gap: 8px; }
  .contact-icon { width: 17px; height: 17px; flex: none; }
</style>
</head>
<body>
  <div class="business-card">
    <svg class="card-shapes" viewBox="0 0 1000 560" aria-hidden="true">
      <path d="M0,455 Q480,230 1000,330 L1000,560 L0,560 Z" fill="var(--band)"/>
      <path d="M20,440 Q480,215 990,300" fill="none" stroke="var(--rule)" stroke-width="4" stroke-linecap="round"/>
    </svg>

    <div class="wordmark">Brevenna<br>Wine Bar</div>

    <div class="restaurant-name">Brevenna Wine Bar &amp; Restaurant</div>

    <div class="contact contact-left">
      <div class="contact-line">
        <svg class="contact-icon" viewBox="0 0 20 20" aria-label="Phone">
          <path d="M5 2 L8 2 L9 6 L7 8 Q9 12 12 13 L14 11 L18 12 L18 15 Q17 18 14 18 Q3 16 2 5 Q2 2 5 2 Z" fill="var(--ink-soft)"/>
        </svg>
        <span>541.555.0172</span>
      </div>
      <div class="contact-line">
        <svg class="contact-icon" viewBox="0 0 20 20" aria-label="Website">
          <circle cx="10" cy="10" r="8" fill="none" stroke="var(--ink-soft)" stroke-width="1.6"/>
          <ellipse cx="10" cy="10" rx="3.5" ry="8" fill="none" stroke="var(--ink-soft)" stroke-width="1.4"/>
          <line x1="2" y1="10" x2="18" y2="10" stroke="var(--ink-soft)" stroke-width="1.4"/>
        </svg>
        <span>brevennawinebar.example</span>
      </div>
    </div>

    <div class="contact contact-right">
      <div>812 4th Ave NW, Calder Bay,</div>
      <div>Norland 00123</div>
    </div>
  </div>
</body>
</html>
```